Wordpress theme website for professionals working together

My partner and I are offering business services, my wife in the energy business as mainly as member of the board of commissioners. I am working as interim manager/consultant in the accounting and finance area. Both activities are connected in one company VELMOT BV (dutch ltd). We need a CV based website. Beside this we do some financial and accounting services.

Target Market(s)

small medium business

Font styles to use
Sans Serif

Colors

Designer to choose colors to be used in the design.

Requirements
Must have
• Pictures of both members.
• CLEAN AND SIMPLE
• I LIKE BLACK & WHITE
Nice to have
• I like design like this theme: http://theme.pruxelo-example.com/resume/

```html
<!DOCTYPE html>
<html lang="en">
<head>
<meta charset="utf-8">
<title>VELMOT BV – Peter Haling</title>
<link href="https://fonts.googleapis.com/css2?family=Montserrat:wght@400;600;700&family=Open+Sans:wght@400;600&display=swap" rel="stylesheet">
<style>
:root{
  --ink:#111;
  --dark:#1b1b1b;
  --darker:#0d0d0d;
  --card:#2a2a2a;
  --mid:#555;
  --muted:#777;
  --line:#cfcfcf;
  --light:#e5e5e5;
  --white:#fff;
  --accent:#d81e1e;
  --brand:#1d3c7a;
}
*{box-sizing:border-box;margin:0;padding:0}
html,body{width:1200px;height:3863px;overflow:hidden}
body{position:relative;font-family:"Open Sans",Arial,sans-serif;color:var(--ink);background:var(--white)}
h1,h2,h3,h4{font-family:"Montserrat",Arial,sans-serif}

/* nav */
.site-nav{position:absolute;left:0;top:0;width:1200px;height:65px;background:var(--white)}
.brand{position:absolute;left:172px;top:14px;display:flex;align-items:center;gap:10px;font-family:"Montserrat",sans-serif;font-weight:700;font-size:30px;color:var(--brand)}
.brand-square{width:14px;height:14px;background:var(--accent)}
.menu{position:absolute;right:172px;top:26px;display:flex;gap:28px;font-family:"Montserrat",sans-serif;font-size:12px;letter-spacing:1px;color:var(--mid)}
.menu .active{color:var(--ink);font-weight:600}

/* hero */
.hero{position:absolute;left:0;top:65px;width:1200px;height:558px;background:linear-gradient(90deg,#f4f4f4 0%,#e2e2e2 50%,#9a9a9a 100%);overflow:hidden}
.hero-photo{position:absolute;left:618px;top:0;width:582px;height:558px;background:radial-gradient(ellipse at 55% 40%,#cfcfcf 0%,#8a8a8a 45%,#2d2d2d 100%)}
.hero-name{position:absolute;left:172px;top:135px;font-size:46px;font-weight:400;letter-spacing:3px;color:var(--ink)}
.hero-text{position:absolute;left:172px;top:208px;width:395px;font-size:11.5px;line-height:19px;color:#333}
.signature{position:absolute;left:172px;top:388px;width:230px;height:44px;background:linear-gradient(90deg,rgba(0,0,0,.12),rgba(0,0,0,0))}
.profile-link{position:absolute;left:172px;top:443px;display:flex;align-items:center;gap:10px;font-size:14px;color:var(--brand);text-decoration:underline}
.profile-dot{width:34px;height:34px;border-radius:50%;background:var(--brand)}

/* experience */
.experience{position:absolute;left:0;top:623px;width:1200px;height:665px;background:linear-gradient(180deg,#171717,#222 60%,#151515)}
.section-title{position:absolute;left:0;width:1200px;text-align:center;font-size:29px;font-weight:700;letter-spacing:1px}
.experience .section-title{top:58px;color:var(--white)}
.timeline-axis{position:absolute;left:599px;top:150px;width:2px;height:450px;background:#444}
.timeline-end{position:absolute;left:591px;top:595px;width:18px;height:18px;border-radius:50%;background:#555}
.tl-node{position:absolute;left:576px;width:48px;height:48px;border-radius:50%;background:#2b2b2b;border:2px solid #4a4a4a}
.tl-node svg{position:absolute;left:13px;top:13px}
.tl-label{position:absolute;height:30px;padding:0 18px;background:#2f2f2f;color:#eee;font-size:13px;line-height:30px;font-family:"Montserrat",sans-serif}
.tl-label.left{right:648px}
.tl-label.right{left:648px}
.tl-text{position:absolute;width:360px;font-size:11.5px;line-height:19px;color:#cfcfcf}
.tl-text.left{right:648px;text-align:right}
.tl-text.right{left:668px}

/* jobs */
.jobs{position:absolute;left:0;top:1288px;width:1200px;height:535px;background:var(--white)}
.jobs .section-title{top:54px}
.jobs .section-title span{color:var(--mid)}
.job-col{position:absolute;top:140px;width:400px}
.job-col h3{font-size:18px;font-weight:600;letter-spacing:1px}
.job-axis{position:absolute;top:195px;width:1px;background:var(--line)}
.job-title{position:absolute;width:135px;font-family:"Montserrat",sans-serif;font-size:15px;font-weight:600;color:#333;line-height:19px}
.job-dot{position:absolute;width:12px;height:12px;border-radius:50%;background:var(--white);border:2px solid #aaa}
.job-desc{position:absolute;font-size:11px;line-height:19px;color:#333;width:225px}
.job-rule{position:absolute;width:140px;height:1px;background:var(--light)}

/* skills */
.skills{position:absolute;left:0;top:1823px;width:1200px;height:546px;background:var(--light)}
.skills .section-title{top:62px}
.lead{position:absolute;left:310px;width:580px;text-align:center;font-size:11.5px;line-height:20px;color:#333}
.skill{position:absolute;width:381px}
.skill-name{font-family:"Montserrat",sans-serif;font-size:12.5px;font-weight:700;letter-spacing:.5px;margin-bottom:6px}
.skill-bar{position:relative;height:32px;background:#c8c8c8;clip-path:polygon(0 0,94% 0,100% 50%,94% 100%,0 100%)}
.skill-fill{position:absolute;left:0;top:0;height:32px;background:var(--ink)}
.skill-pct{position:absolute;right:36px;top:0;line-height:32px;font-size:12px;font-weight:600;color:#222}

/* facts */
.facts{position:absolute;left:0;top:2369px;width:1200px;height:443px;background:linear-gradient(180deg,#121212,#1c1c1c)}
.fact{position:absolute;top:103px;height:232px;background:var(--card);text-align:center;color:#ddd}
.fact .icon{height:60px;margin-top:38px;display:flex;align-items:center;justify-content:center}
.fact h4{font-size:14px;letter-spacing:1px;color:var(--white);margin-top:22px;margin-bottom:8px}
.fact p{font-size:13px;line-height:20px;color:#bbb}

/* portfolio */
.portfolio{position:absolute;left:0;top:2812px;width:1200px;height:754px;background:var(--white)}
.portfolio .section-title{top:60px}
.shot{position:absolute;height:227px}
.btn-more{position:absolute;left:546px;top:690px;width:108px;height:36px;background:var(--ink);color:var(--white);font-family:"Montserrat",sans-serif;font-size:11px;font-weight:600;letter-spacing:1px;line-height:36px;text-align:center}

/* footer */
.site-footer{position:absolute;left:0;top:3566px;width:1200px;height:297px;background:var(--darker);color:#bbb}
.foot-col{position:absolute;top:40px}
.foot-col h4{font-size:18px;font-weight:600;color:var(--white);margin-bottom:14px}
.foot-col li{list-style:none;font-size:11px;line-height:20px;color:#999}
.newsletter{position:absolute;left:708px;top:82px;display:flex}
.newsletter .field{width:240px;height:28px;border-radius:14px 0 0 14px;background:var(--white);font-size:11px;color:#aaa;line-height:28px;padding-left:14px}
.newsletter .signup{width:82px;height:28px;border-radius:0 14px 14px 0;background:var(--accent);color:var(--white);font-size:11px;font-weight:600;line-height:28px;text-align:center}
.socials{position:absolute;left:712px;top:140px;display:flex;gap:28px}
.socials span{width:20px;height:20px;border-radius:50%;background:var(--white)}
.foot-rule{position:absolute;left:172px;top:232px;width:856px;height:1px;background:#2a2a2a}
.copyright{position:absolute;left:0;top:256px;width:1200px;text-align:center;font-size:11px;color:#bbb}
.page-code{position:absolute;right:72px;top:258px;font-size:11px;color:#888}
</style>
</head>
<body>

<header class="site-nav">
  <div class="brand"><span>VELMOT BV</span><span class="brand-square"></span></div>
  <nav class="menu"><span class="active">HOME</span><span>ELSA</span><span>SKILLS</span><span>EXPERIENCE</span><span>PORTFOLIO</span><span>EDUCATION</span><span>CONTACT</span></nav>
</header>

<section class="hero">
  <div class="hero-photo" role="img" aria-label="Black and white portrait photo of Peter Haling"></div>
  <h1 class="hero-name">PETER HALING</h1>
  <p class="hero-text">Sed ut perspiciatis unde omnis iste natus error sit voluptatem accusa ntium doloremque laudantium, totam rem aperiam, eaque ipsa quae ab illo inventore veritatis et quasi architecto beatae vitae dicta sunlot explicabo. Nemo enim ipsam voluptatem quia voluptas sit aspernatur aut odit aut fugit, sed quia consequuntur magni dolores eos qui ration e voluptatem sequi nesciunt. Neque porro quisquam est, qui dolorem ipsum quia dolor sit amet, consectetur.</p>
  <div class="signature" role="img" aria-label="Handwritten signature of Peter Haling"></div>
  <div class="profile-link"><span class="profile-dot"></span><span>Profile</span></div>
</section>

<section class="experience">
  <h2 class="section-title">EXPERIENCE</h2>
  <div class="timeline-axis"></div>
  <div class="timeline-end"></div>

  <div class="tl-label left" style="top:160px">Accounting 2012</div>
  <div class="tl-node" style="top:151px"><svg width="18" height="18" viewBox="0 0 18 18"><rect x="2" y="3" width="14" height="13" fill="none" stroke="#aaa" stroke-width="1.5"/><line x1="2" y1="7" x2="16" y2="7" stroke="#aaa" stroke-width="1.5"/></svg></div>
  <p class="tl-text right" style="top:151px">Sed ut perspiciatis unde omnis iste natus error sit voluptatem accusa ntiumdolor emque laudantium, totam reed ut perspiciatis unde omnis iste nats error sit voluptatem accusa</p>

  <p class="tl-text left" style="top:228px">Sed ut perspiciatis unde omnis iste natus error sit voluptatem accusa ntiumdolor emque laudantium, totam reed ut perspiciatis unde omnis iste nats error sit voluptatem accusa</p>
  <div class="tl-node" style="top:236px"><svg width="18" height="18" viewBox="0 0 18 18"><circle cx="6" cy="7" r="3" fill="none" stroke="#aaa" stroke-width="1.5"/><circle cx="12" cy="7" r="3" fill="none" stroke="#aaa" stroke-width="1.5"/><path d="M1 16c1-4 9-4 10 0M7 16c1-4 9-4 10 0" fill="none" stroke="#aaa" stroke-width="1.5"/></svg></div>
  <div class="tl-label right" style="top:245px">Team player 2015</div>

  <div class="tl-label left" style="top:335px">Trouble shooter 2014</div>
  <div class="tl-node" style="top:326px"><svg width="18" height="18" viewBox="0 0 18 18"><path d="M2 9l14-6-5 14-2-6z" fill="none" stroke="#aaa" stroke-width="1.5"/></svg></div>
  <p class="tl-text right" style="top:326px">Sed ut perspiciatis unde omnis iste natus error sit voluptatem accusa ntiumdolor emque laudantium, totam reed ut perspiciatis unde omnis iste nats error sit voluptatem accusa</p>

  <p class="tl-text left" style="top:404px">Sed ut perspiciatis unde omnis iste natus error sit voluptatem accusa ntiumdolor emque laudantium, totam reed ut perspiciatis unde omnis iste nats error sit voluptatem accusa</p>
  <div class="tl-node" style="top:414px"><svg width="18" height="18" viewBox="0 0 18 18"><path d="M3 15C3 7 8 3 16 3c0 8-4 12-12 12z" fill="none" stroke="#aaa" stroke-width="1.5"/></svg></div>
  <div class="tl-label right" style="top:423px">Project management 2016</div>

  <div class="tl-label left" style="top:510px">Financial Reporter 2018</div>
  <div class="tl-node" style="top:501px"><svg width="18" height="18" viewBox="0 0 18 18"><path d="M2 15l5-6 4 3 5-8" fill="none" stroke="#aaa" stroke-width="1.5"/></svg></div>
  <p class="tl-text right" style="top:501px">Sed ut perspiciatis unde omnis iste natus error sit voluptatem accusa ntiumdolor emque laudantium, totam reed ut perspiciatis unde omnis iste nats error sit voluptatem accusa</p>
</section>

<section class="jobs">
  <h2 class="section-title">PETER <span>JOBS</span></h2>

  <div class="job-col" style="left:172px"><h3>ACTUAL JOBS</h3></div>
  <div class="job-axis" style="left:327px;height:285px"></div>
  <div class="job-title" style="left:172px;top:220px">Advisor Rivant</div>
  <div class="job-dot" style="left:321px;top:224px"></div>
  <p class="job-desc" style="left:353px;top:202px">Sed ut perspiciatis unde omnis iste nasus error sit voluptatem accusa ntiumdolor emque laudantium, totam rem.</p>
  <div class="job-rule" style="left:172px;top:275px"></div>
  <div class="job-title" style="left:172px;top:298px">Advisor Brook &amp;<br>Vale</div>
  <div class="job-dot" style="left:321px;top:312px"></div>
  <p class="job-desc" style="left:353px;top:290px">Sed ut perspiciatis unde omnis iste ntus error sit voluptatem accusa ntiumdolor emque laudantium, totam rem</p>
  <p class="job-desc" style="left:353px;top:365px">Sed ut perspiciatis unde omnis iste nats error sit voluptatem accusa ntiumdolor emque laudantium, totam rem.ed upers picatis unde omnis iste natus error sit voluptatem accusa ntiumdolor</p>

  <div class="job-col" style="left:631px"><h3>FINISHED JOBS</h3></div>
  <div class="job-axis" style="left:789px;height:220px"></div>
  <div class="job-title" style="left:631px;top:205px">Controller<br>a.i. Rivant</div>
  <div class="job-dot" style="left:783px;top:224px"></div>
  <p class="job-desc" style="left:811px;top:202px">Sed ut perspiciatis unde omnis iste natus error sit voluptatem accusa ntiumdolor emque laudantium, totam rem.</p>
  <div class="job-title" style="left:631px;top:296px">Advisor Delta<br>Groen</div>
  <div class="job-dot" style="left:783px;top:312px"></div>
  <p class="job-desc" style="left:811px;top:290px">Sed ut perspiciatis unde omnis iste natus error sit voluptatem accusa ntiumdolor emque laudantium, totam rem.</p>
  <div class="job-title" style="left:631px;top:386px">Financial<br>director Nordel</div>
  <div class="job-dot" style="left:783px;top:402px"></div>
  <p class="job-desc" style="left:811px;top:380px">Sed ut perspiciatis unde omnis iste natus error sit voluptatem accusa ntiumdolor emque laudantium, totam rem.</p>
</section>

<section class="skills">
  <h2 class="section-title">SKILLS</h2>
  <p class="lead" style="top:110px">Sed ut perspiciatis unde omnis iste natus error sit voluptatem accusa ntiumdolor emque laudantium, totam remd ut perspiciatis unde omnis iste ntus error sit voluptatem accusa ntiumdolor emque lauda</p>

  <div class="skill" style="left:172px;top:186px"><div class="skill-name">ANNUAL REPORTING</div><div class="skill-bar"><div class="skill-fill" style="width:75%"></div><span class="skill-pct">80%</span></div></div>
  <div class="skill" style="left:172px;top:254px"><div class="skill-name">FINANCIAL MONTHLY REPORTING</div><div class="skill-bar"><div class="skill-fill" style="width:58%"></div><span class="skill-pct">40%</span></div></div>
  <div class="skill" style="left:172px;top:324px"><div class="skill-name">ACCOUNTING</div><div class="skill-bar"><div class="skill-fill" style="width:82%"></div><span class="skill-pct" style="right:28px">90%</span></div></div>
  <div class="skill" style="left:172px;top:392px"><div class="skill-name">FINANCIAL MANAGEMENT</div><div class="skill-bar"><div class="skill-fill" style="width:64%"></div><span class="skill-pct">70%</span></div></div>

  <div class="skill" style="left:641px;top:186px"><div class="skill-name">PROJECT MANAGEMENT</div><div class="skill-bar"><div class="skill-fill" style="width:64%"></div><span class="skill-pct">70%</span></div></div>
  <div class="skill" style="left:641px;top:254px"><div class="skill-name">TEAM PLAYER</div><div class="skill-bar"><div class="skill-fill" style="width:78%"></div><span class="skill-pct">80%</span></div></div>
  <div class="skill" style="left:641px;top:324px"><div class="skill-name">TROUBLE SHOOTER</div><div class="skill-bar"><div class="skill-fill" style="width:78%"></div><span class="skill-pct">80%</span></div></div>
  <div class="skill" style="left:641px;top:392px"><div class="skill-name">ETC.</div><div class="skill-bar"><div class="skill-fill" style="width:40%"></div><span class="skill-pct">30%</span></div></div>
</section>

<section class="facts">
  <div class="fact" style="left:172px;width:273px">
    <div class="icon"><svg width="70" height="50" viewBox="0 0 70 50"><path d="M35 8C27 3 14 3 4 6v40c10-3 23-3 31 2 8-5 21-5 31-2V6C56 3 43 3 35 8zM35 8v40" fill="none" stroke="#ddd" stroke-width="2"/></svg></div>
    <h4>EDUCATION</h4><p>Accounting Institute (RA)<br>Atheneum B</p>
  </div>
  <div class="fact" style="left:466px;width:270px">
    <div class="icon"><svg width="60" height="60" viewBox="0 0 60 60"><path d="M8 52L30 30M30 30l6-6a9 9 0 0 1 14-12l-7 7 3 5 5 3 7-7a9 9 0 0 1-12 14l-6 6M10 8l42 42M8 12l4-4 6 6-4 4z" fill="none" stroke="#ddd" stroke-width="2"/></svg></div>
    <h4>WORKED FOR</h4><p>Kade Advocaten &amp; Notarissen<br>Veldkamp Audit</p>
  </div>
  <div class="fact" style="left:757px;width:271px">
    <div class="icon"><svg width="66" height="56" viewBox="0 0 66 56"><rect x="3" y="3" width="60" height="50" fill="none" stroke="#ddd" stroke-width="2"/><circle cx="22" cy="20" r="5" fill="none" stroke="#ddd" stroke-width="2"/><path d="M3 44l18-14 12 10 10-8 20 16" fill="none" stroke="#ddd" stroke-width="2"/></svg></div>
    <h4>OTHER</h4><p>Fotography</p>
  </div>
</section>

<section class="portfolio">
  <h2 class="section-title">PORTFOLIO</h2>
  <p class="lead" style="top:116px">Sed ut perspiciatis unde omnis iste ntus error sit voluptatem accusa ntiumdolor emque laudantium, totam remd ut perspiciatis unde omnis iste ntus error sit voluptatem accusa ntiumdolor emque lauda</p>
  <div class="shot" style="left:172px;top:193px;width:279px;background:linear-gradient(135deg,#8a7a6a,#d8d4cc)" role="img" aria-label="Photo of a desk with papers, charts and coffee"></div>
  <div class="shot" style="left:461px;top:193px;width:278px;background:linear-gradient(135deg,#2e4e78,#9fb7d2)" role="img" aria-label="Photo of a businessman with a rising chart"></div>
  <div class="shot" style="left:747px;top:193px;width:281px;background:linear-gradient(135deg,#e0ddd8,#8c8680)" role="img" aria-label="Photo of hands reviewing a laptop and documents"></div>
  <div class="shot" style="left:172px;top:430px;width:279px;background:linear-gradient(135deg,#1f2a3a,#7d8796)" role="img" aria-label="Photo of a businessman using a tablet"></div>
  <div class="shot" style="left:461px;top:430px;width:278px;background:linear-gradient(135deg,#c9a27a,#5a5048)" role="img" aria-label="Photo of hands typing on a laptop"></div>
  <div class="shot" style="left:747px;top:430px;width:281px;background:linear-gradient(135deg,#eef0f0,#9a8e82)" role="img" aria-label="Photo of two colleagues working at a laptop"></div>
  <div class="btn-more">VIEW MORE</div>
</section>

<footer class="site-footer">
  <div class="foot-col" style="left:172px"><h4>Company</h4><ul><li>Sed ut perspiciatis</li><li>Unde omnis iste</li><li>Voluptatem</li><li>Accusantium</li><li>Doloremque</li><li>Laudantium</li></ul></div>
  <div class="foot-col" style="left:351px"><h4>About</h4><ul><li>Sed ut perspiciatis</li><li>Unde omnis iste</li><li>Voluptatem</li><li>Accusantium</li><li>Doloremque</li><li>Laudantium</li></ul></div>
  <div class="foot-col" style="left:517px"><h4>Links</h4><ul><li>Sed ut perspiciatis</li><li>Unde omnis iste</li><li>Voluptatem</li><li>Accusantium</li><li>Doloremque</li><li>Laudantium</li></ul></div>
  <div class="foot-col" style="left:708px"><h4>Newsletter</h4></div>
  <div class="newsletter"><div class="field">Email</div><div class="signup">SIGN UP</div></div>
  <div class="socials"><span></span><span></span><span></span><span></span></div>
  <div class="foot-rule"></div>
  <p class="copyright">© 2018 All Rights Are Reserved Terms of Use | Privacy Policy</p>
  <span class="page-code">C4</span>
</footer>

</body>
</html>
```